Poster

I need a poster for my business, www.coastalsupperroutesnerja.example which some information about the most important activities (Sangria Tasting, Iberian Ham, Charcuteries & Sherry Wine Tasting, Sailboat Experiences and Picnic Experiences). A3 Format. Social media included (@coastalsupperroutescsr), contact information included.

```html
<!DOCTYPE html>
<html lang="en">
<head>
<meta charset="utf-8">
<title>Coastal Supper Routes Nerja – Poster</title>
<link href="https://fonts.googleapis.com/css2?family=Oswald:wght@500;600&family=Montserrat:ital,wght@0,500;1,500&family=Kaushan+Script&display=swap" rel="stylesheet">
<style>
  :root {
    --stage: #e4e4e2;
    --paper: #ffffff;
    --amber: #f0a021;
    --ink: #2f2f2f;
    --white: #ffffff;
    --shade: rgba(40, 52, 66, 0.55);
    --chat-green: #3dbb4c;
  }
  * { margin: 0; padding: 0; box-sizing: border-box; }
  html, body { width: 1200px; height: 1200px; overflow: hidden; background: var(--stage); }
  .poster {
    position: absolute; left: 198px; top: 30px;
    width: 804px; height: 1140px;
    background: var(--paper);
    overflow: hidden;
    box-shadow: 0 6px 24px rgba(0,0,0,0.18);
  }
  .hero-photo {
    position: absolute; left: 0; top: 0; width: 804px; height: 571px;
    background:
      radial-gradient(ellipse at 70% 30%, rgba(255,214,150,0.95) 0%, rgba(236,160,80,0.6) 25%, rgba(0,0,0,0) 55%),
      linear-gradient(160deg, #27465e 0%, #4a6b82 35%, #c9a27a 60%, #2c3b4a 100%);
  }
  .hero-shade {
    position: absolute; left: 57px; top: 215px; width: 277px; height: 356px;
    background: var(--shade);
  }
  .brand-box {
    position: absolute; left: 29px; top: 39px; width: 329px; height: 176px;
    background: var(--paper);
    display: flex; align-items: center; gap: 18px; padding-left: 30px;
  }
  .brand-square { width: 46px; height: 46px; background: var(--amber); flex: none; }
  .brand-name {
    font-family: "Oswald", sans-serif; font-weight: 500;
    font-size: 29px; line-height: 1.12; color: var(--ink); text-transform: uppercase;
    white-space: nowrap;
  }
  .headline {
    position: absolute; left: 76px; top: 236px;
    font-family: "Oswald", sans-serif; font-weight: 600;
    font-size: 116px; line-height: 0.9; color: var(--white);
    letter-spacing: -2px;
  }
  .headline-script {
    position: absolute; left: 100px; top: 420px;
    font-family: "Kaushan Script", cursive;
    font-size: 96px; color: var(--amber); transform: rotate(-10deg);
  }
  .activities {
    position: absolute; left: 38px; top: 571px; width: 524px; height: 403px;
    background: var(--amber);
  }
  .activity {
    position: absolute;
    border-left: 2px solid var(--white);
    padding-left: 11px;
    font-family: "Oswald", sans-serif; font-weight: 500;
    font-size: 45px; line-height: 1.03; color: var(--white);
    text-transform: uppercase;
  }
  .gallery-photo { position: absolute; left: 562px; width: 204px; height: 126px; }
  .gallery-photo.tasting { top: 505px; background: linear-gradient(135deg, #8c8a88, #dcd7d2 60%, #7b2a2a); }
  .gallery-photo.tapas { top: 635px; background: linear-gradient(160deg, #b49474, #3a2c25 55%, #181614); }
  .gallery-photo.host { top: 765px; background: linear-gradient(180deg, #4f6a4a, #d6b48b 50%, #3c3a38); }
  .gallery-photo.picnic { top: 894px; background: linear-gradient(180deg, #6f9ab9, #a9c3d6 45%, #c9b59a); }
  .contact-phone {
    position: absolute; left: 38px; top: 994px;
    display: flex; align-items: center; gap: 14px;
  }
  .chat-dot { width: 62px; height: 62px; border-radius: 50%; background: var(--chat-green); flex: none; }
  .phone-number {
    font-family: "Oswald", sans-serif; font-weight: 600;
    font-size: 58px; line-height: 1; color: var(--ink); white-space: nowrap;
  }
  .website {
    position: absolute; left: 48px; top: 1072px;
    font-family: "Oswald", sans-serif; font-weight: 500;
    font-size: 25px; line-height: 1; color: var(--ink); text-transform: uppercase;
    white-space: nowrap;
  }
  .website .domain { color: var(--amber); }
  .social {
    position: absolute; left: 556px; top: 1040px; width: 216px;
    display: flex; flex-direction: column; align-items: center; gap: 10px;
  }
  .social-dot { width: 30px; height: 30px; border-radius: 50%; background: var(--amber); }
  .social-handle {
    font-family: "Montserrat", sans-serif; font-weight: 500; font-style: italic;
    font-size: 13px; color: var(--ink); white-space: nowrap;
  }
</style>
</head>
<body>
  <main class="poster">
    <div class="hero-photo" role="img" aria-label="Couple on the bow of a sailboat at sunset on the sea, sails lit in orange"></div>
    <div class="hero-shade"></div>

    <div class="brand-box">
      <div class="brand-square"></div>
      <div class="brand-name">Coastal Supper<br>Routes Nerja</div>
    </div>

    <h1 class="headline">ENJOY<br>YOUR</h1>
    <div class="headline-script">Day</div>

    <section class="activities">
      <div class="activity" style="left:32px; top:44px;">Sangria<br>Tasting</div>
      <div class="activity" style="left:232px; top:44px;">Sailboat<br>Experiences</div>
      <div class="activity" style="left:32px; top:160px;">Iberian<br>Ham</div>
      <div class="activity" style="left:232px; top:160px;">Picnic<br>Experiences</div>
      <div class="activity" style="left:32px; top:277px;">Charcuteries &amp;<br>Sherry Wine Tasting</div>
    </section>

    <div class="gallery-photo tasting" role="img" aria-label="Friends sharing glasses of sangria outdoors"></div>
    <div class="gallery-photo tapas" role="img" aria-label="Olives and tapas served on a dark bar counter"></div>
    <div class="gallery-photo host" role="img" aria-label="Host in an apron cooking paella for guests in front of a wine shelf"></div>
    <div class="gallery-photo picnic" role="img" aria-label="Picnic basket with bread and wine on a blanket by the sea"></div>

    <div class="contact-phone">
      <div class="chat-dot"></div>
      <div class="phone-number">+34 600 12 34 56</div>
    </div>
    <div class="website">www.<span class="domain">coastalsupperroutesnerja</span>.example</div>

    <div class="social">
      <div class="social-dot"></div>
      <div class="social-handle">@coastalsupperroutescsr</div>
    </div>
  </main>
</body>
</html>
```